Maris Dovey Studio Business Cards

Hi - using the information and logo provided I require a two sided business card designed with the following information. The business card is a 'mini card' 3.5" x 1.25".

Front of card should be the logo attached but inverted (so the background is the peach colour and the logo white).

Back should have these details. If we can't fit the Pictogrum and Friendwall part can we just put the little logos.

Tessa Varnold

Art and Design Consultant
Dealer - Curator - Events - Styling - Creative Sourcing

P: 0438 217 604
E: tessa@marisdoveystudio.example
W: www.marisdoveystudio.example
I (pictogram image please): marisdoveystudio F (Friendwall image please): MarisDoveyAdviser

Target Market(s)

Galleries, artists, art buyers, interior design clients, event managers, creative types

Industry/Entity Type

Business

```html
<!DOCTYPE html>
<html lang="en">
<head>
<meta charset="utf-8">
<title>Maris Dovey Studio – Business Cards</title>
<link rel="stylesheet" href="https://fonts.googleapis.com/css2?family=Tinos:wght@400&display=swap">
<style>
  :root {
    --backdrop: #6b5a51;
    --card-dark: #0b0b0b;
    --card-glow: #3a3a3a;
    --card-light: #ffffff;
    --peach: #f0b59a;
    --ink: #111111;
    --white: #ffffff;
    --muted: #8a8a8a;
    --rule-dark: #4a4a4a;
    --rule-light: #d6d6d6;
    --icon: #3a3a3a;
  }
  html, body {
    margin: 0;
    padding: 0;
    width: 1200px;
    height: 960px;
    overflow: hidden;
    background: var(--backdrop);
    font-family: "Tinos", "Times New Roman", serif;
  }
  .board {
    position: relative;
    width: 1200px;
    height: 960px;
  }
  .card {
    position: absolute;
    height: 306px;
    overflow: hidden;
  }

  /* Front */
  .card-front {
    left: 48px;
    top: 60px;
    width: 854px;
    background: radial-gradient(ellipse 260px 200px at 438px 90px, var(--card-glow) 0%, #1a1a1a 45%, var(--card-dark) 100%);
  }
  .front-mark {
    position: absolute;
    left: 392px;
    top: 30px;
    width: 92px;
    height: 92px;
    border-radius: 50%;
    background: var(--peach);
  }
  .front-brand {
    position: absolute;
    left: 0;
    right: 0;
    top: 160px;
    margin: 0;
    text-align: center;
    font-size: 27px;
    font-weight: 400;
    letter-spacing: 5px;
    text-transform: uppercase;
    color: var(--peach);
    padding-left: 22px;
  }
  .front-rule {
    position: absolute;
    left: 90px;
    width: 684px;
    height: 1px;
    background: var(--rule-dark);
  }
  .front-rule.r1 { top: 209px; }
  .front-rule.r2 { top: 248px; }
  .front-rule.r3 { top: 286px; }
  .front-name {
    position: absolute;
    left: 90px;
    width: 684px;
    top: 212px;
    margin: 0;
    text-align: center;
    font-size: 28px;
    font-weight: 400;
    color: var(--white);
    line-height: 34px;
  }
  .front-name .role { font-size: 23px; }
  .front-services {
    position: absolute;
    left: 90px;
    width: 684px;
    top: 253px;
    margin: 0;
    text-align: center;
    font-size: 17px;
    color: var(--muted);
    line-height: 22px;
  }

  /* Back */
  .card-back {
    left: 300px;
    top: 466px;
    width: 857px;
    background: var(--card-light);
  }
  .back-rule {
    position: absolute;
    height: 2px;
    background: var(--rule-light);
  }
  .back-rule.top { left: 30px; width: 798px; top: 26px; }
  .back-rule.social-top { left: 32px; width: 800px; top: 227px; }
  .back-rule.social-bottom { left: 32px; width: 800px; top: 277px; }
  .back-mark {
    position: absolute;
    left: 118px;
    top: 62px;
    width: 84px;
    height: 84px;
    border-radius: 50%;
    background: var(--peach);
  }
  .back-brand {
    position: absolute;
    left: 40px;
    width: 240px;
    top: 160px;
    margin: 0;
    text-align: center;
    font-size: 21px;
    font-weight: 400;
    color: var(--peach);
  }
  .contact-list {
    position: absolute;
    left: 298px;
    top: 72px;
    margin: 0;
    padding: 0;
    list-style: none;
    font-size: 22px;
    color: var(--ink);
  }
  .contact-list li {
    height: 40px;
    line-height: 30px;
  }
  .social-row {
    position: absolute;
    left: 0;
    top: 228px;
    width: 857px;
    height: 49px;
    font-size: 25px;
    color: var(--ink);
  }
  .social-icon {
    position: absolute;
    top: 10px;
    width: 31px;
    height: 31px;
    border-radius: 3px;
    background: var(--icon);
  }
  .social-icon.pictogrum { left: 50px; }
  .social-icon.friendwall { left: 493px; }
  .social-handle {
    position: absolute;
    top: 9px;
    line-height: 30px;
  }
  .social-handle.pictogrum { left: 100px; }
  .social-handle.friendwall { left: 550px; }
  .social-divider {
    position: absolute;
    left: 436px;
    top: 9px;
    line-height: 30px;
    font-size: 24px;
    color: var(--ink);
  }
</style>
</head>
<body>
<main class="board">

  <section class="card card-front" aria-label="Business card front">
    <div class="front-mark" aria-hidden="true"></div>
    <h1 class="front-brand">Maris Dovey Studio</h1>
    <div class="front-rule r1"></div>
    <p class="front-name">Tessa Varnold <span class="role">(Art and Design Consultant)</span></p>
    <div class="front-rule r2"></div>
    <p class="front-services">Dealer | Curator | Events | Styling | Creative Sourcing</p>
    <div class="front-rule r3"></div>
  </section>

  <section class="card card-back" aria-label="Business card back">
    <div class="back-rule top"></div>
    <div class="back-mark" aria-hidden="true"></div>
    <p class="back-brand">Maris Dovey Studio</p>
    <ul class="contact-list">
      <li>Phone: 0438 217 604</li>
      <li>Email: tessa@marisdoveystudio.example</li>
      <li>Web: www.marisdoveystudio.example</li>
    </ul>
    <div class="back-rule social-top"></div>
    <div class="social-row">
      <span class="social-icon pictogrum" aria-hidden="true"></span>
      <span class="social-handle pictogrum">MarisDoveyAdviser</span>
      <span class="social-divider">|</span>
      <span class="social-icon friendwall" aria-hidden="true"></span>
      <span class="social-handle friendwall">marisdoveystudio</span>
    </div>
    <div class="back-rule social-bottom"></div>
  </section>

</main>
</body>
</html>
```